New Service Brochure for The Brellford Spa

Hi All! We are looking for a new brochure design- tri-fold, double sided, and full color. We are a certified Tallow Spa for men and women in the heart of the Catskill Mountains of upstate New York. Our clients would describe us as laid back luxury with no pretensions and a home away from home vibe. Our font is Avalon. Key colors are black, white and gold. Looking for an inviting, clean, and modern/minimalist spread with a touch of elegance. No orchid imagery, please. I would like our "Tallow Spa" logo on cover, too please. Front cover image with with logo and "Tallow Spa" Sticker . Bottom of back with contact info. We would prefer massages go on left inside page, facials in middle and right inside, nails on back left, but we are open to new or different layout proposals. Thank you!

Target Market(s)

Men & Women.

Industry/Entity Type

Health And Wellness

Other font styles liked:
• Avalon is our signature font

Requirements
Must have
• Easy on the eyes.
Nice to have
• Negative space.
Should not have
• No orchids. Busy lines and wild colors.

```html
<!DOCTYPE html>
<html lang="en">
<head>
<meta charset="utf-8">
<title>The Brellford Spa – Service Brochure</title>
<link href="https://fonts.googleapis.com/css2?family=Cormorant+Garamond:wght@500&family=Raleway:wght@300;400;500&display=swap" rel="stylesheet">
<style>
  :root{
    --backdrop:#d9d9db;
    --cream:#fbf8f4;
    --ink:#1c1c1c;
    --gold:#c9a55a;
    --gold-soft:#d8b874;
    --charcoal-1:#232323;
    --charcoal-2:#3b3b3b;
    --paper-text:#3a3a3a;
    --on-dark:#e8e4dc;
    --on-dark-muted:#bdb8ae;
  }
  *{margin:0;padding:0;box-sizing:border-box}
  html,body{width:787px;height:1200px;overflow:hidden}
  body{background:var(--backdrop);font-family:'Raleway',sans-serif;color:var(--paper-text);position:relative}

  .sheet{position:absolute;left:52px;width:656px;height:510px;background:var(--cream);box-shadow:0 10px 14px -6px rgba(0,0,0,.35);overflow:hidden}
  .sheet--outside{top:60px}
  .sheet--inside{top:608px}
  .block{position:absolute}

  .dark{background:linear-gradient(160deg,var(--charcoal-2),var(--charcoal-1) 70%);color:var(--on-dark)}
  .gold-rule{position:absolute;left:0;width:100%;height:3px;background:var(--gold)}
  .photo{position:absolute}

  /* wordmark */
  .wordmark{font-family:'Cormorant Garamond',serif;font-weight:500;text-align:center;line-height:.95;letter-spacing:1px}
  .wordmark--cover{color:var(--ink);font-size:30px}
  .wordmark--panel{color:var(--on-dark);font-size:30px}
  .tagline{font-size:8px;text-align:center;font-weight:400}

  .heading{font-weight:300;color:var(--gold);font-size:11.5px}
  .heading--dark{color:var(--on-dark);font-size:12px}
  .intro{font-size:6.3px;line-height:1.35;color:var(--gold);text-align:justify}
  .intro--dark{color:var(--gold-soft)}

  .menu{list-style:none}
  .menu li{margin-bottom:0}
  .item-head{display:flex;align-items:baseline;font-size:5.6px;color:var(--gold);gap:1px}
  .item-head .leader{flex:1;border-bottom:1px dotted var(--gold);transform:translateY(-1px);opacity:.8}
  .item-desc{font-size:4.3px;line-height:1.35;margin-top:2px}
  .dark .item-desc{color:var(--on-dark)}
  .paper .item-desc{color:#444}

  .subhead{font-size:6.3px;color:var(--gold);letter-spacing:.2px}
  .rates{font-size:6.5px;line-height:1.72;color:var(--on-dark)}
  .rates span{color:var(--gold)}
  .rates--two{display:grid;grid-template-columns:1fr 1fr;line-height:1.72}

  .contact{text-align:center;font-size:8.6px;line-height:1.65;color:var(--on-dark)}
  .cta{display:inline-block;background:var(--gold);color:#fff;font-size:8px;padding:4px 12px;letter-spacing:.3px}
  .hours{text-align:center;font-size:8.2px;line-height:1.75;color:#555}
  .hours h3{font-weight:400;font-size:8px;letter-spacing:.8px;margin-bottom:2px}
  .escape{text-align:center;color:var(--ink);font-size:12.5px;line-height:1.45;font-weight:300}
  .escape a{display:block;color:var(--gold);font-size:9px;text-decoration:none;margin-top:5px}

  .partner{display:flex;align-items:center;gap:4px;font-size:5px;color:var(--ink);line-height:1.25;letter-spacing:.3px}
  .partner i{display:block;width:22px;height:22px;background:var(--gold)}
</style>
</head>
<body>

<!-- Outside of the brochure -->
<section class="sheet sheet--outside">

  <div class="block paper" style="left:0;top:0;width:219px;height:139px;padding:14px 9px 0 7px">
    <div class="partner" style="position:absolute;right:8px;top:12px"><i></i><span>VERDANE<br>ORGANIC<br>SKINCARE</span></div>
    <h2 class="heading" style="margin-top:24px">Hands &amp; feet</h2>
    <p class="intro" style="margin-top:15px">Melt into a Pedicure Throne in our Nail Lounge. Our handmade soaks and scrubs are made in house with only the freshest natural and organic ingredients! Your hands and feet have never been loved like this! All nail services include nail and cuticle care, massage and polish of choice.</p>
  </div>

  <div class="photo" role="img" aria-label="Bright nail lounge with a white pedicure throne and soaking basin" style="left:219px;top:0;width:218px;height:139px;background:linear-gradient(135deg,#f3e2cf,#e9cdb0 45%,#f7efe6)"></div>

  <div class="block" style="left:437px;top:0;width:219px;height:139px;background:var(--cream)">
    <div class="wordmark wordmark--cover" style="margin-top:30px">The<br>Brellford Spa</div>
    <p class="tagline" style="margin-top:20px;color:var(--ink)">a boutique spa for Men &amp; Women</p>
  </div>

  <div class="block dark" style="left:0;top:139px;width:437px;height:284px"></div>

  <ul class="block menu dark" style="left:7px;top:155px;width:205px;background:none">
    <li style="height:36px"><div class="item-head">Organic Eight Greens Manicure<span class="leader"></span>$65</div><p class="item-desc">Hydrate, smooth and clarify tired hands. Stone crop cleansing oil, eight greens exfoliant and lotus detox hand treatment. 55 minutes.</p></li>
    <li style="height:36px"><div class="item-head">Hot Stone Manicure<span class="leader"></span>$65</div><p class="item-desc">Heal and smooth tired hands with our signature keratin and copaiba hot herbal mitts. 55 minutes.</p></li>
    <li style="height:36px"><div class="item-head">Reverse The Hands Of Time Manicure<span class="leader"></span>$75</div><p class="item-desc">The name says it all. Smoothing lava scrub, brightening masque and luscious tightening hand creme. 55 minutes.</p></li>
    <li style="height:36px"><div class="item-head">Palo Santo Pedicure<span class="leader"></span>$85</div><p class="item-desc">Includes our bespoke bergamot and balsam foot soak, refreshing peppermint scrub and Palo Santo lotion. 55 minutes.</p></li>
    <li style="height:38px"><div class="item-head">Brellford Spa Pedicure<span class="leader"></span>$75</div><p class="item-desc">In addition to a classic pedicure, a soothing anti-inflammatory mud mask, paraffin wrap and revitalizing foot and calf massage. Topped off with your choice of enamel. 55 minutes.</p></li>
    <li style="height:42px"><div class="item-head">Mother of Dragonfruit Pedicure<span class="leader"></span>$85</div><p class="item-desc">Breaker of calluses, reliever of tired feet, queen of the cuticle. Spring cleaning and perfectly polished toes. Soak, scrub, cuticle and nail care, hot stone foot and leg massage, polish. 55 minutes.</p></li>
    <li><div class="item-head">Grapefruit and Pine Pedicure<span class="leader"></span>$45</div><p class="item-desc">A perfect pick me up for any feet that want to celebrate the season! Soak, scrub, cuticle and nail care, polish. 30 minutes.</p></li>
  </ul>

  <div class="block" style="left:219px;top:139px;width:218px;height:284px;text-align:center">
    <div class="wordmark wordmark--panel" style="margin-top:40px">The<br>Brellford Spa</div>
    <p class="tagline" style="margin-top:19px;color:var(--on-dark-muted)">a boutique spa for Men &amp; Women</p>
    <div style="margin-top:19px"><span class="cta">GET IN TOUCH</span></div>
    <address class="contact" style="margin-top:14px;font-style:normal">
      (518) 555-0142<br>info@thebrellfordspa.com<br>42 Alder Brook Road<br>Brellford, NY 12400<br>Just off Main Street!
    </address>
  </div>

  <div class="photo" role="img" aria-label="Guest relaxing on a massage table with rolled white towels" style="left:437px;top:139px;width:219px;height:284px;background:linear-gradient(120deg,#3a2a1f,#a37a57 40%,#e3c3a1 70%,#f4e6d6)"></div>
  <div class="photo" role="img" aria-label="Tallow Spa certification badge" style="left:602px;top:380px;width:48px;height:48px;border-radius:50%;background:#4a8a2f"></div>

  <div class="gold-rule" style="top:423px"></div>

  <div class="photo" role="img" aria-label="Feet resting in a pedicure basin with red toenail polish" style="left:0;top:426px;width:219px;height:84px;background:linear-gradient(110deg,#6b4a3c,#d7b8a3 45%,#f2ece8)"></div>

  <div class="block hours" style="left:219px;top:440px;width:218px">
    <h3>HOURS</h3>
    Thurs-Sat: 10am-6pm<br>Sun-Mon: 10am-5pm<br>Tues &amp; Wed: Closed
  </div>

  <div class="block escape" style="left:437px;top:447px;width:219px">
    ESCAPE THE CONGESTION OF<br>EVERYDAY LIFE!
    <a href="#">www.thebrellfordspa.com</a>
  </div>
</section>

<!-- Inside of the brochure -->
<section class="sheet sheet--inside">

  <div class="block dark" style="left:0;top:0;width:219px;height:376px;padding:28px 8px 0 8px">
    <h2 class="heading heading--dark">Massages</h2>
    <p class="intro intro--dark" style="margin-top:9px;font-size:6.8px;line-height:1.25">Tired, sore muscles, and exhausted minds are refreshed by the perfect massage customized to your individual needs.</p>
    <ul class="menu" style="margin-top:10px">
      <li style="height:34px"><div class="item-head">Swedish Massage<span class="leader"></span>$105/$160</div><p class="item-desc">Relaxing and therapeutic. Ease tension and enhance circulation. Great for a first time massage or any spa veteran. 55min - 90min</p></li>
      <li style="height:34px"><div class="item-head">Deep Tissue<span class="leader"></span>$115/$175</div><p class="item-desc">A therapeutic combination of slow and deep pressure alleviates chronic pain, muscle fatigue and limited range of motion. 55min - 90min</p></li>
      <li style="height:28px"><div class="item-head">Tension Tamer<span class="leader"></span>$125/$195</div><p class="item-desc">Head, neck and shoulders. Deep tissue with hot towels, muscle soothing oils and cupping. 55min - 90min</p></li>
      <li style="height:34px"><div class="item-head">Hot Stone<span class="leader"></span>$175</div><p class="item-desc">Unforgettable. Warm basalt lava stones melt away all stress and tension in sore muscles and joints. The ultimate après ski treat. 90min</p></li>
      <li style="height:28px"><div class="item-head">Recovery<span class="leader"></span>$110/$170</div><p class="item-desc">Specific to your athletic needs, whether pro or weekend warrior. Relax, stretch and recover. 55min - 90min</p></li>
      <li style="height:40px"><div class="item-head">Restora Rapid Recovery Massage<span class="leader"></span>$135</div><p class="item-desc">Ideal for runners, cyclists, hikers, skiers and riders. Recover faster and feel better with compression chamber sleeves. Includes head, neck, shoulders, arm and hand massage. 55 minutes.</p></li>
      <li style="height:28px"><div class="item-head">Prenatal<span class="leader"></span>$110</div><p class="item-desc">Ultimate treat for mothers-to-be. Soothes aches and pains during pregnancy. Mother must be out of first trimester. 55 minutes.</p></li>
      <li><div class="item-head">Couples<span class="leader"></span>$210 &amp; up</div><p class="item-desc">For lovebirds or loved ones. Relax and recoup with your favorite person. 55 or 90 minutes.</p></li>
    </ul>
  </div>

  <div class="gold-rule" style="top:376px;width:219px"></div>
  <div class="photo" role="img" aria-label="Guests celebrating with a tiered tray of treats" style="left:0;top:379px;width:219px;height:131px;background:linear-gradient(120deg,#f6eee6,#e2c4a8 40%,#b98a6c 70%,#efe3d7)"></div>

  <div class="photo" role="img" aria-label="Close-up of a woman with glowing skin" style="left:219px;top:0;width:218px;height:137px;background:linear-gradient(135deg,#fbf7f3,#ecd3bd 45%,#d9b494 70%,#f5ece3)"></div>

  <div class="block paper" style="left:219px;top:137px;width:218px;height:373px;padding:2px 8px 0 11px;background:#fff">
    <h2 class="heading">Facials</h2>
    <p class="intro" style="margin-top:5px;font-size:6.3px;line-height:1.25">Featuring Verdane Organic Skincare products our organic and biodynamic facials are perfect for even the most sensitive skin!</p>
    <ul class="menu" style="margin-top:11px">
      <li style="height:31px"><div class="item-head">Detox Facial<span class="leader"></span>$135</div><p class="item-desc">Increases oxygen and blood flow to dramatically reboot your skin's natural healing abilities and reveal healthier skin. 55 minutes.</p></li>
      <li style="height:31px"><div class="item-head">B.L.T. Facial<span class="leader"></span>$145</div><p class="item-desc">Organic triple peel, also known as our "Runway Peel" because it leaves you glowing and ready for the red carpet immediately. 55 minutes.</p></li>
      <li style="height:31px"><div class="item-head">Double Down Facial<span class="leader"></span>$165</div><p class="item-desc">Organic triple peel, also known as our "Runway Peel" because it leaves you glowing and ready for the red carpet immediately. 55 minutes.</p></li>
      <li style="height:40px"><div class="item-head">Organic Masque Montage<span class="leader"></span>$115</div><p class="item-desc">Three layers of customized masques created exclusively for your skin type. Includes steam, cleanse, exfoliation, extractions, masques, massage and moisturizer. 55 minutes.</p></li>
      <li style="height:34px"><div class="item-head">Calm Skin Facial<span class="leader"></span>$125</div><p class="item-desc">Combat redness, irritation and dryness. Gentle, yet effective for even the most sensitive skin types. Soothe, hydrate and refresh. 55 mins</p></li>
      <li style="height:54px"><div class="item-head">R&amp;R Facial<span class="leader"></span>$255 (Reg. $275)</div><p class="item-desc">Our most dynamic results oriented facial, and the ultimate kick start to rebooting skin after a long summer of sunshine and heat, or smoking. Make sure you are ready for years younger when you see your skin. Microdermabrasion, double peel facial, LED light emitting diode boom. (as in WOW!) 90 minutes.</p></li>
      <li style="height:40px"><div class="item-head">Mangosteen Facial<span class="leader"></span>$135</div><p class="item-desc">Minimize pore size and surface build up with zero down time. Our organic lactic acid peel leaves skin smooth, clarified and glowing! Custom masque included. Ideal for all skin types. 55 minutes.</p></li>
      <li><div class="item-head">Microdermabrasion<span class="leader"></span>$115</div><p class="item-desc">Reduce wrinkles, scarring, discoloration, sun damage, large pores and age spots. Stimulate collagen and elastin production through diamond and crystal exfoliation. Best in series of six. 30min.</p></li>
    </ul>
  </div>

  <div class="block dark" style="left:437px;top:0;width:219px;height:376px;padding:28px 9px 0 12px">
    <h2 class="heading heading--dark">Hair Removal</h2>
    <h3 class="subhead" style="margin-top:8px;font-weight:400">ELECTROLYSIS</h3>
    <p class="intro intro--dark" style="margin-top:1px;font-size:6.3px;line-height:1.25">Say goodbye to unwanted and embarrassing hair with the only FDA approved method of Permanent Hair Removal. Great for men and women of all ages.</p>
    <div class="rates" style="margin-top:5px">
      15 Minutes - <span>$25</span><br>30 Minutes - <span>$45</span><br>45 Minutes - <span>$60</span><br>60 Minutes - <span>$75</span><br>4 Hour Bonus Pack - <span>$240</span>
    </div>
    <h3 class="subhead" style="margin-top:20px;font-weight:400">WAXING</h3>
    <p class="intro intro--dark" style="margin-top:1px;font-size:6.3px;line-height:1.25">Using only the best wax in the world, our custom blends of French and domestic waxes make for a flawless waxing experience. From eyebrows to Brazilians, your comfort and care is our priority.</p>
    <div class="rates rates--two" style="margin-top:13px">
      <div>Lips - <span>$12</span><br>Chin - <span>$12</span><br>Eyebrows - <span>$15</span><br>Sideburns - <span>$20</span><br>Lower Half Leg - <span>$30</span><br>Upper Half Leg - <span>$40</span><br>Full Leg - <span>$65</span><br>Bikini (top &amp; sides) - <span>$50</span></div>
      <div>Brazilian - <span>$65+</span><br>Chest - <span>$30+</span><br>Back - <span>$35+</span><br>Underarm - <span>$28</span><br>Half Arm - <span>$25</span><br>Full Arm - <span>$38</span><br>Feet - <span>$10</span><br>Hands - <span>$8</span></div>
    </div>
  </div>

  <div class="gold-rule" style="top:376px;left:437px;width:219px"></div>
  <div class="photo" role="img" aria-label="Hot stone massage on a guest's back" style="left:437px;top:379px;width:219px;height:131px;background:linear-gradient(120deg,#5a3b2a,#c79a76 40%,#e9cfb6 70%,#f6ece2)"></div>
</section>

</body>
</html>
```